Business card for Sports Apparel business

DOUBLE SIDED DESIGN
We need business cards for a new sports apparel business. We are developing a protective headband for soccer initially.
Torvalle is focused on designing and developing head protection products to reduce the likelihood of concussion when playing sports. Exploring and understanding medical insights, material science research, current and former players experiences and governing bodies guidelines has allowed Torvalle to develop the safety, style, form and function requirements of a suitable product to bring to market.
Target Market(s)
Mums buying kits for the sons and daughters. Amateur footballers.
Industry/Entity Type
Sporting Good
Contact Information for Business Card
Martin Ashworth - CEO
Mobile: +44 7431589027
Email: martin@torvalle.co.uk
Tel: 0208 5519372
Helena Pargeter - COO
Mob: +44 7385 640117
Email: helena@torvalle.co.uk
Tel: 0208 5519372
Duncan Farrow - CCO
Mob: +44 7564 293081
Email: duncan@torvalle.co.uk
Tel: 0208 5519372
Look and feel
Each slider illustrates characteristics of the customer's brand and the style your logo design should communicate.

```html
<!DOCTYPE html>
<html lang="en">
<head>
<meta charset="utf-8">
<title>Torvalle Business Card</title>
<link rel="stylesheet" href="https://fonts.googleapis.com/css2?family=Montserrat:wght@400;500;700&display=swap">
<style>
  :root {
    --backdrop: #2e2f31;
    --card: #ffffff;
    --brand-blue: #19609a;
    --ink-grey: #585858;
    --ink-dark: #3a3a3a;
  }
  * { margin: 0; padding: 0; box-sizing: border-box; }
  html, body {
    width: 1200px;
    height: 900px;
    overflow: hidden;
    background: var(--backdrop);
    font-family: "Montserrat", Arial, sans-serif;
  }
  .card {
    position: absolute;
    left: 250px;
    width: 700px;
    height: 400px;
    background: var(--card);
    border-bottom: 9px solid var(--brand-blue);
    box-shadow: 0 14px 30px rgba(0,0,0,0.45);
  }
  .card--front { top: 30px; }
  .card--back { top: 462px; }

  .brand {
    position: absolute;
    left: 0; right: 0;
    display: flex;
    align-items: center;
    justify-content: center;
    gap: 18px;
  }
  .brand__square {
    background: var(--brand-blue);
  }
  .brand__name {
    color: var(--ink-grey);
    font-weight: 700;
    letter-spacing: 0.04em;
    text-transform: uppercase;
    line-height: 1;
  }
  .card--front .brand { top: 140px; }
  .card--front .brand__square { width: 48px; height: 48px; }
  .card--front .brand__name { font-size: 74px; }

  .card--back .brand { top: 46px; gap: 12px; }
  .card--back .brand__square { width: 26px; height: 26px; }
  .card--back .brand__name { font-size: 40px; }

  .website {
    position: absolute;
    left: 0; right: 0;
    text-align: center;
    color: var(--ink-dark);
    font-weight: 500;
    letter-spacing: 0.12em;
  }
  .website__domain { color: var(--brand-blue); }
  .card--front .website { bottom: 22px; font-size: 19px; }

  .person {
    position: absolute;
    top: 135px;
    left: 0; right: 0;
    text-align: center;
  }
  .person__name {
    color: var(--brand-blue);
    font-weight: 700;
    font-size: 26px;
    letter-spacing: 0.08em;
    text-transform: uppercase;
  }
  .person__role {
    color: var(--ink-grey);
    font-size: 20px;
    letter-spacing: 0.08em;
    margin-top: 2px;
  }

  .divider {
    position: absolute;
    top: 226px;
    left: 0; right: 0;
    height: 2px;
    background: var(--brand-blue);
  }
  .contact-icons {
    position: absolute;
    top: 208px;
    left: 0; right: 0;
    display: flex;
    justify-content: center;
    gap: 10px;
  }
  .contact-icons svg { width: 38px; height: 38px; display: block; }

  .contact-list {
    position: absolute;
    top: 258px;
    left: 0; right: 0;
    list-style: none;
    text-align: center;
    color: var(--ink-dark);
    font-size: 21px;
    letter-spacing: 0.08em;
    line-height: 30px;
  }
  .contact-list .website__domain { color: var(--brand-blue); }
</style>
</head>
<body>

<section class="card card--front">
  <div class="brand">
    <span class="brand__square"></span>
    <span class="brand__name">Torvalle</span>
  </div>
  <p class="website">www.<span class="website__domain">torvalle</span>.co.uk</p>
</section>

<section class="card card--back">
  <div class="brand">
    <span class="brand__square"></span>
    <span class="brand__name">Torvalle</span>
  </div>

  <div class="person">
    <p class="person__name">Helena Pargeter</p>
    <p class="person__role">COO</p>
  </div>

  <div class="divider"></div>

  <div class="contact-icons">
    <svg viewBox="0 0 38 38" aria-label="Telephone">
      <circle cx="19" cy="19" r="18" fill="#19609a"/>
      <path d="M13 10c1-1 2-1 3 0l2 3c.5 1 .3 1.8-.5 2.4l-1 .8c.8 2.3 2.6 4.6 4.6 5.8l1-.9c.8-.7 1.6-.8 2.4-.2l3 2c1 .8 1 1.8 0 2.8l-1.5 1.5c-1.3 1.3-4 1-7-1.2-3.5-2.6-6.6-6.7-7.4-10-.5-2 0-3.5 1-4.5z" fill="#fff"/>
    </svg>
    <svg viewBox="0 0 38 38" aria-label="Mobile">
      <circle cx="19" cy="19" r="18" fill="#19609a"/>
      <rect x="13" y="8" width="12" height="22" rx="2" fill="none" stroke="#fff" stroke-width="2"/>
      <line x1="13" y1="25" x2="25" y2="25" stroke="#fff" stroke-width="1.6"/>
      <circle cx="19" cy="27.5" r="1" fill="#fff"/>
    </svg>
    <svg viewBox="0 0 38 38" aria-label="Email">
      <circle cx="19" cy="19" r="18" fill="#19609a"/>
      <rect x="9" y="12" width="20" height="14" rx="1.5" fill="none" stroke="#fff" stroke-width="2"/>
      <polyline points="9.5,13 19,20.5 28.5,13" fill="none" stroke="#fff" stroke-width="2"/>
    </svg>
    <svg viewBox="0 0 38 38" aria-label="Website">
      <circle cx="19" cy="19" r="18" fill="#19609a"/>
      <g fill="none" stroke="#fff" stroke-width="1.6">
        <circle cx="19" cy="19" r="10"/>
        <ellipse cx="19" cy="19" rx="4.5" ry="10"/>
        <line x1="9" y1="19" x2="29" y2="19"/>
        <line x1="11" y1="14" x2="27" y2="14"/>
        <line x1="11" y1="24" x2="27" y2="24"/>
      </g>
    </svg>
  </div>

  <ul class="contact-list">
    <li>0208 5519372</li>
    <li>+44 7385 640117</li>
    <li>helena@torvalle.co.uk</li>
    <li>www.<span class="website__domain">torvalle</span>.co.uk</li>
  </ul>
</section>

</body>
</html>
```